Business card design for a dynamic IT consulting company

We need a business card design for a young firm, specialized in the Telecommunications/Consulting industry. The name of the company is Quindor and Partners Business Consulting Ltd. (Short name: Quindor and Partnes)
Quindor = solve read reverse, so we aim to be uncomplicated and solution-oriented. The small pipe in our logo is also related to the word solve. So we need a new business card design, which is simple, eye catching and something non traditional (I would probably prefer a square shaped design rather than a rectangle, but open for suggestions). Attached our logo.

Target Market(s)

Usually our customers are Tier1 Telecoms providers (Q-Netra, Palorix, etc) and their executives.

Industry/Entity Type

Business

Contact Information for Business Card

Name: Bence Tolnavari
Email: b.tolnavari@quindor.hu
Web: www.quindor.hu
Mobile: +36 30 518 2769
Title: Managing Director

Optional:
Company name: Quindor and Partners Ltd.
Address: 1087 Budapest, Tolvenka str. 28/C, Hungary

Font styles to use
Other font styles liked:
• helveticaneue_medium, Prime Regular are used now.

Colors

Designer to choose colors to be used in the design.

Requirements
Must have
• I would like to have a 2 sided design.
Nice to have
• I thought if we make the logo a bit bigger (without the company name), that could go to the back with the company name below. I though, if the pipe in the logo is somehow touchable on the business card, would be nice and unique.

```html
<!DOCTYPE html>
<html lang="en">
<head>
<meta charset="utf-8">
<title>Quindor and Partners – Business Card</title>
<link rel="stylesheet" href="https://fonts.googleapis.com/css2?family=Exo+2:wght@400&family=Arimo:wght@400&display=swap">
<style>
  :root {
    --page-bg: #e9e6e1;
    --card-white: #ffffff;
    --card-dark: #4a4b4d;
    --ink-grey: #4d4e50;
    --brand-blue: #1b9ad6;
    --tint-blue: #dcecf7;
    --tint-pink: #f6e3ef;
    --tint-grey: #efefef;
  }
  * { margin: 0; padding: 0; box-sizing: border-box; }
  html, body { width: 1200px; height: 1200px; overflow: hidden; }
  body {
    background: var(--page-bg);
    position: relative;
    font-family: "Arimo", Arial, sans-serif;
  }
  .card {
    position: absolute;
    left: 150px;
    width: 900px;
    height: 520px;
    border-radius: 6px;
    box-shadow: 0 10px 30px rgba(0,0,0,0.12);
    overflow: hidden;
  }
  .card-front { top: 60px; background: var(--card-white); }
  .card-back { top: 620px; background: var(--card-dark); }

  .front-pattern {
    position: absolute;
    right: 0; top: 0;
    width: 340px; height: 100%;
    background: linear-gradient(160deg, var(--tint-grey) 0%, var(--tint-blue) 45%, var(--tint-pink) 100%);
    opacity: 0.6;
  }

  .wordmark {
    display: flex;
    align-items: center;
    gap: 14px;
  }
  .wordmark-square {
    width: 20px; height: 20px;
    background: var(--ink-grey);
    flex: none;
  }
  .wordmark-name {
    font-family: "Arimo", Arial, sans-serif;
    font-weight: 400;
    font-size: 44px;
    color: var(--ink-grey);
    line-height: 1;
  }

  .front-brand { position: absolute; left: 64px; top: 80px; }

  .person { position: absolute; left: 64px; top: 215px; }
  .person-name {
    font-family: "Exo 2", sans-serif;
    font-weight: 400;
    font-size: 40px;
    color: var(--brand-blue);
  }
  .person-title {
    font-size: 24px;
    color: var(--ink-grey);
    margin-top: 4px;
  }

  .contact { position: absolute; left: 64px; top: 345px; }
  .contact-line {
    font-size: 22px;
    color: var(--ink-grey);
    line-height: 1.45;
  }
  .contact-label { color: var(--brand-blue); }
  .contact-rule {
    height: 2px;
    background: var(--brand-blue);
    margin: 10px 0;
    width: 500px;
  }
  .contact-address { font-size: 22px; color: var(--ink-grey); }

  .back-brand {
    position: absolute;
    left: 0; right: 0; top: 210px;
    display: flex;
    flex-direction: column;
    align-items: center;
  }
  .card-back .wordmark-square { background: #ffffff; }
  .card-back .wordmark-name { color: #ffffff; font-size: 56px; }
  .legal-name {
    font-size: 20px;
    letter-spacing: 0.3em;
    color: #ffffff;
    margin-top: 22px;
  }
</style>
</head>
<body>

  <section class="card card-front" aria-label="Business card front">
    <div class="front-pattern" role="img" aria-label="Soft pattern of pale blue, pink and grey squares"></div>

    <div class="front-brand">
      <div class="wordmark">
        <span class="wordmark-square"></span>
        <span class="wordmark-name">Quindor and Partners</span>
      </div>
    </div>

    <div class="person">
      <div class="person-name">Bence Tolnavari</div>
      <div class="person-title">Managing Director</div>
    </div>

    <div class="contact">
      <div class="contact-line"><span class="contact-label">M:</span> +36 30 518 2769 | <span class="contact-label">E:</span> b.tolnavari@quindor.hu</div>
      <div class="contact-line"><span class="contact-label">W:</span> www.quindor.hu</div>
      <div class="contact-rule"></div>
      <div class="contact-address">1087 Budapest, Tolvenka str. 28/C, Hungary</div>
    </div>
  </section>

  <section class="card card-back" aria-label="Business card back">
    <div class="back-brand">
      <div class="wordmark">
        <span class="wordmark-square"></span>
        <span class="wordmark-name">Quindor</span>
      </div>
      <div class="legal-name">Quindor and Partners Ltd.</div>
    </div>
  </section>

</body>
</html>
```